EB-5 Regional Center needs a Web design

Harlow Ridge Financial Partners is an expanding EB-r regional center. We have been successful in sponsoring multiple projects of third-party developers and placing EB-5, B-1, and Private Investments into multiple projects.

We are now partnering directly with project developers in the energy and healthcare to raise foreign capital for projects in those industries. The foreign capital is used as project equity and our collective balance sheets are used to guarantee debt to complete the funding of the projects.

We need a web site where we can post our company credentials, the bios of each partner, a document page for each of our projects where we can post specific project related documents which foreign investors can read, and we will need a section where foreign investors can fill out investor forms confirming that they are qualified investors and leaving their contact so that our agents and executives can make contact.

The final design should reflect the exceptional experience of the partners and our financial strength and stability.

We do have a logo we would want to use on the web design.

Target Market(s)

EB-5 Investors, B-1 Investors, Private Equity and other investors seeking quality investment in job creating US projects.

Coding

Number of Pages Required

5+ page

Font styles to use
Sans Serif

Requirements
Must have
• Pages to display company info, partner bios, projects completed, and a projects in-process page where we can post documents and info on projects for which we are seeking foreign investment. We also need a section where investors can enter their qualifying personal information and leave contact information for us.

```html
<!DOCTYPE html>
<html lang="en">
<head>
<meta charset="utf-8">
<title>Harlow Ridge Financial Partners</title>
<link href="https://fonts.googleapis.com/css2?family=Barlow:wght@400;500;600;700&display=swap" rel="stylesheet">
<style>
:root{
  --blue:#2a5bc8;
  --blue-dark:#2451b5;
  --ink:#1c1c1c;
  --text:#555;
  --hero:#141517;
  --footer:#171717;
  --panel:#f4f4f4;
  --line:#e4e4e4;
  --white:#fff;
}
*{margin:0;padding:0;box-sizing:border-box}
html,body{width:1200px;height:3717px;overflow:hidden}
body{font-family:"Barlow",sans-serif;color:var(--ink);background:var(--white);position:relative}
.abs{position:absolute}
a{text-decoration:none;color:inherit}

/* header + hero */
.hero{left:0;top:0;width:1200px;height:767px;
  background:
    radial-gradient(circle at 597px 300px,rgba(235,235,225,.85) 0,rgba(220,210,185,.45) 55px,rgba(0,0,0,0) 120px),
    radial-gradient(ellipse 330px 150px at 560px 260px,rgba(210,120,50,.45),rgba(0,0,0,0) 100%),
    radial-gradient(ellipse 260px 330px at 930px 360px,rgba(120,80,60,.55),rgba(0,0,0,0) 100%),
    radial-gradient(ellipse 380px 90px at 560px 95px,rgba(110,80,60,.5),rgba(0,0,0,0) 100%),
    radial-gradient(ellipse 500px 120px at 600px 470px,rgba(150,100,70,.35),rgba(0,0,0,0) 100%),
    radial-gradient(ellipse at 50% 40%,#2c2723 0%,#1a1a1b 55%,var(--hero) 85%)}
.brand{left:111px;top:24px;display:flex;align-items:center;gap:12px;color:var(--white);font-size:21px;font-weight:600;line-height:1}
.brand-mark{width:34px;height:34px;border-radius:50%;background:var(--white)}
.nav{top:38px;left:0;width:1200px;font-size:13px;font-weight:500;color:var(--white)}
.nav a{position:absolute;white-space:nowrap}
.nav .active{color:#6e96ff}
.hero-arrow{width:34px;height:34px;border:2px solid var(--white);border-radius:50%;top:367px}
.hero-title{left:0;width:1200px;text-align:center;color:var(--white);font-weight:700;text-transform:uppercase}

/* service cards */
.card{top:710px;width:312px;height:409px;background:var(--white);border:1px solid var(--line);border-top:3px solid var(--blue);text-align:center}
.card-photo{height:200px}
.card h3{margin-top:28px;font-size:22px;font-weight:500}
.card p{margin:14px auto 0;width:260px;font-size:14px;line-height:27.5px;color:var(--text)}
.card .more{display:block;margin-top:10px;font-size:14px;font-weight:600;color:var(--blue)}

/* about */
.about-h{left:652px;top:1250px;font-size:44px;font-weight:500;color:#333}
.about-lead{left:652px;top:1317px;width:440px;font-size:19.5px;line-height:33px;color:var(--blue);font-weight:500}
.about-body{left:652px;top:1403px;width:408px;font-size:14px;line-height:27.4px;color:var(--text);text-align:justify}
.btn{display:flex;align-items:center;justify-content:center;font-size:17px;font-weight:500;text-transform:uppercase}
.btn-blue{background:var(--blue);color:var(--white)}
.btn-white{background:var(--white);color:var(--blue)}

/* consultation */
.band{left:0;top:1861px;width:1200px;height:540px;
  background:
    radial-gradient(ellipse 300px 160px at 200px 420px,rgba(255,255,255,.09),rgba(255,255,255,0) 100%),
    radial-gradient(ellipse 260px 140px at 520px 120px,rgba(255,255,255,.07),rgba(255,255,255,0) 100%),
    linear-gradient(160deg,#2b5ccb,#2451b5 60%,#2a58c4)}
.consult-kicker{left:147px;top:1988px;font-size:26px;color:var(--white)}
.consult-h{left:147px;top:2020px;font-size:40px;font-weight:500;color:var(--white)}
.consult-p{left:147px;top:2090px;width:375px;font-size:13.5px;line-height:26px;color:var(--white)}
.form{left:649px;top:1798px;width:431px;height:603px;background:var(--white);border:1px solid var(--line);border-top:5px solid var(--blue)}
.form h2{position:absolute;top:42px;width:100%;text-align:center;font-size:30px;font-weight:500;color:#333}
.rule{height:3px;background:var(--blue)}
.field{left:32px;width:366px;background:var(--panel);border:1px solid #ddd;font-size:14px;color:#333;padding:14px 15px}

/* project */
.section-h{font-size:46px;font-weight:500;color:#1b1b1b}
.section-h span{color:var(--blue)}
.proj-p{left:111px;top:2600px;width:280px;font-size:13.5px;line-height:26px;color:var(--text)}
.proj-more{left:111px;top:2726px;font-size:14px;font-weight:600;color:var(--blue)}
.proj-photo{top:2452px;width:259px;height:350px}
.small-arrow{width:30px;height:30px;border:2px solid var(--white);border-radius:50%;top:2610px}

/* team */
.team{left:0;top:2870px;width:1200px;height:517px;background:#f6f6f6}
.team-sub{left:0;top:2988px;width:1200px;text-align:center;font-size:13.5px;color:#222}
.member{top:3037px;width:231px;height:299px;background:var(--white);border:1px solid var(--line);text-align:center}
.member-photo{height:231px}
.member b{display:block;margin-top:20px;font-size:17px;font-weight:500}
.member small{display:block;margin-top:4px;font-size:13px;color:var(--text)}

/* footer */
.footer{left:0;top:3387px;width:1200px;height:330px;background:var(--footer);color:var(--white)}
.f-brand{left:111px;top:3470px;width:330px;display:flex;align-items:center;gap:14px;font-size:22px;line-height:26px;font-weight:500;color:#bbb}
.f-brand i{flex:none;width:44px;height:44px;background:#bbb;display:block;border-radius:50%}
.social{top:3566px;width:36px;height:36px;border:2px solid var(--white);border-radius:50%}
.f-copy{left:111px;top:3656px;font-size:14px}
.f-h{top:3436px;font-size:21px;font-weight:500}
.f-links{left:496px;top:3480px;list-style:none;font-size:13px;line-height:27.4px}
.f-links li::before{content:"»";display:inline-block;width:38px;font-size:15px}
.f-text{left:691px;top:3482px;width:390px;font-size:16px;line-height:27px}
.f-input{left:692px;top:3564px;width:385px;height:50px;background:var(--white);color:#555;font-size:15px;padding:15px 16px;border-radius:2px}
</style>
</head>
<body>

<!-- hero -->
<div class="abs hero" role="img" aria-label="Hands cupping a glowing light bulb with a network of orange lines"></div>
<div class="abs brand"><span class="brand-mark"></span>Harlow Ridge Financial Partners</div>
<nav class="abs nav">
  <a class="active" style="left:541px">HOME</a>
  <a style="left:622px">ABOUT US</a>
  <a style="left:731px">SERVICES</a>
  <a style="left:838px">PROJECT</a>
  <a style="left:943px">BIO</a>
  <a style="left:1010px">CONTACT US</a>
</nav>
<div class="abs hero-arrow" style="left:33px"><svg width="30" height="30" viewBox="0 0 30 30"><path d="M17 9l-6 6 6 6" fill="none" stroke="#fff" stroke-width="2.5"/></svg></div>
<div class="abs hero-arrow" style="left:1122px"><svg width="30" height="30" viewBox="0 0 30 30"><path d="M13 9l6 6-6 6" fill="none" stroke="#fff" stroke-width="2.5"/></svg></div>
<div class="abs hero-title" style="top:444px;font-size:38px">Harlow Ridge</div>
<div class="abs hero-title" style="top:494px;font-size:49px">Financial Partners</div>

<!-- service cards -->
<article class="abs card" style="left:111px">
  <div class="card-photo" role="img" aria-label="Traders at a desk with many monitors" style="background:radial-gradient(ellipse 90px 60px at 60px 55px,rgba(170,180,210,.55),rgba(0,0,0,0)),radial-gradient(ellipse 110px 50px at 230px 160px,rgba(90,150,220,.6),rgba(0,0,0,0)),radial-gradient(ellipse 120px 50px at 80px 165px,rgba(70,120,200,.55),rgba(0,0,0,0)),linear-gradient(180deg,#3a4668 0%,#1d2747 55%,#141d38 100%)"></div>
  <h3>Investment</h3>
  <p>Sed ut perspiciatis unde omnis iste natus error sit voluptatem accusantium dolem udantium totam aperiam</p>
  <a class="more">READ MORE »</a>
</article>
<article class="abs card" style="left:444px">
  <div class="card-photo" role="img" aria-label="Business team talking in a meeting room" style="background:radial-gradient(ellipse 90px 110px at 240px 90px,rgba(170,140,120,.7),rgba(0,0,0,0)),radial-gradient(ellipse 80px 60px at 120px 120px,rgba(150,120,100,.55),rgba(0,0,0,0)),radial-gradient(ellipse 160px 60px at 150px 20px,rgba(220,225,232,.8),rgba(0,0,0,0)),linear-gradient(180deg,#a7afbb 0%,#6e7889 50%,#3b4456 100%)"></div>
  <h3>Business</h3>
  <p>Sed ut perspiciatis unde omnis iste natus error sit voluptatem accusantium dolem udantium totam aperiam</p>
  <a class="more">READ MORE »</a>
</article>
<article class="abs card" style="left:777px">
  <div class="card-photo" role="img" aria-label="Hand holding a glowing cube network" style="background:radial-gradient(ellipse 90px 70px at 130px 110px,rgba(200,215,255,.7),rgba(0,0,0,0)),radial-gradient(ellipse 100px 80px at 240px 80px,rgba(150,140,170,.55),rgba(0,0,0,0)),linear-gradient(135deg,#243a86 0%,#3a56b4 45%,#7f95d8 100%)"></div>
  <h3>Solution</h3>
  <p>Sed ut perspiciatis unde omnis iste natus error sit voluptatem accusantium dolem udantium totam aperiam</p>
  <a class="more">READ MORE »</a>
</article>

<!-- about -->
<svg class="abs" style="left:0;top:1130px" width="1200" height="720" viewBox="0 1130 1200 720">
  <defs>
    <linearGradient id="coinTone" x1="0" y1="0" x2="0.35" y2="1">
      <stop offset="0" stop-color="#0e0e0e"/>
      <stop offset="0.28" stop-color="#3a302a"/>
      <stop offset="0.45" stop-color="#d8b7a0"/>
      <stop offset="0.62" stop-color="#e9d6c8"/>
      <stop offset="0.75" stop-color="#b89a6e"/>
      <stop offset="0.86" stop-color="#dfe3ea"/>
      <stop offset="1" stop-color="#f3f5f9"/>
    </linearGradient>
    <pattern id="stripes" width="8" height="8" patternUnits="userSpaceOnUse" patternTransform="rotate(45)">
      <rect width="8" height="8" fill="#fafafa"/><rect width="1" height="8" fill="#ececec"/>
    </pattern>
  </defs>
  <polygon points="1200,1130 1200,1700 830,1720" fill="url(#stripes)"/>
  <polygon points="0,1300 60,1300 150,1560 0,1700" fill="url(#stripes)"/>
  <polygon points="575,1207 543,1264 608,1264" fill="#eeeeee"/>
  <polygon points="287,1191 614,1620 287,1833 0,1560 0,1540" fill="url(#coinTone)" role="img" aria-label="Hand stacking coins in rising piles"/>
</svg>
<h2 class="abs about-h">ABOUT US</h2>
<p class="abs about-lead">Sed ut perspiciatis unde omnis iste natus error sit accusantium doloremque</p>
<p class="abs about-body">Nemo enim ipsam voluptatem quia voluptas sit aspernatur aut odit aut fugit, sed quia consequuntur magni dolores eos qui ratione voluptatem sequi nesciunt. Neque porro quisquam est, qui dolorem ipsum quia dolor sit amet, consectetur, adipisci velit, sed quia non numquam eius modi tempora incidunt ut labore et dolore magnam aliquam quaerat voluptatem.</p>
<a class="abs btn btn-blue" style="left:652px;top:1601px;width:161px;height:53px">Read More</a>

<!-- consultation -->
<div class="abs band" role="img" aria-label="Blue-toned photo of a desk with papers"></div>
<p class="abs consult-kicker">Contact Us To Get</p>
<h2 class="abs consult-h">A Free Consultation</h2>
<p class="abs consult-p">Sed ut perspiciatis unde omnis iste natus error sit voluptatem accusantium doloremque laudantium, totam rem aperiam, ea que ipsa quae ab illo inventore veritatis</p>
<a class="abs btn btn-white" style="left:147px;top:2213px;width:162px;height:53px">Read More</a>

<form class="abs form">
  <h2>GET A REQUEST</h2>
  <div class="abs rule" style="left:188px;top:88px;width:54px"></div>
  <div class="abs field" style="top:120px;height:50px">Name :</div>
  <div class="abs field" style="top:180px;height:51px">Email :</div>
  <div class="abs field" style="top:241px;height:50px">Phone :</div>
  <div class="abs field" style="top:301px;height:127px">Message :</div>
  <div class="abs btn btn-blue" style="left:32px;top:447px;width:366px;height:51px">Submit</div>
</form>

<!-- project -->
<h2 class="abs section-h" style="left:111px;top:2506px">OUR <span>PROJECT</span></h2>
<div class="abs rule" style="left:111px;top:2565px;width:79px"></div>
<p class="abs proj-p">Sed ut perspiciatis unde omnis iste natus error sit voluptatem accusantium doloremque lauda ntium totam rem aperiam, eaque ipsa quae ab ntore veritatis et quasi architecto</p>
<a class="abs proj-more">VIEW MORE »</a>
<div class="abs proj-photo" style="left:423px;background:radial-gradient(ellipse 120px 70px at 150px 150px,rgba(210,215,220,.7),rgba(0,0,0,0)),radial-gradient(ellipse 90px 60px at 60px 40px,rgba(60,55,50,.6),rgba(0,0,0,0)),radial-gradient(ellipse 130px 50px at 130px 320px,rgba(150,140,120,.6),rgba(0,0,0,0)),linear-gradient(170deg,#7e7a76 0%,#9a9793 45%,#5b5753 100%)" role="img" aria-label="Hands using a tablet at a desk"></div>
<div class="abs proj-photo" style="left:682px;background:radial-gradient(ellipse 130px 110px at 150px 210px,rgba(235,240,248,.85),rgba(0,0,0,0)),radial-gradient(ellipse 90px 70px at 70px 60px,rgba(50,80,140,.7),rgba(0,0,0,0)),linear-gradient(160deg,#4d6aa2 0%,#8ea3c9 50%,#d0d9e7 100%)" role="img" aria-label="Pen over printed financial charts"></div>
<div class="abs proj-photo" style="left:941px;width:259px;background:radial-gradient(ellipse 70px 140px at 40px 120px,rgba(180,190,170,.55),rgba(0,0,0,0)),radial-gradient(ellipse 90px 80px at 200px 170px,rgba(140,100,75,.6),rgba(0,0,0,0)),radial-gradient(ellipse 120px 60px at 110px 300px,rgba(70,70,70,.7),rgba(0,0,0,0)),linear-gradient(160deg,#7b7b6a 0%,#54534a 55%,#2d2c28 100%)" role="img" aria-label="Colleagues smiling around a laptop"></div>
<div class="abs small-arrow" style="left:429px"><svg width="26" height="26" viewBox="0 0 26 26"><path d="M15 8l-5 5 5 5" fill="none" stroke="#fff" stroke-width="2"/></svg></div>
<div class="abs small-arrow" style="left:1163px"><svg width="26" height="26" viewBox="0 0 26 26"><path d="M11 8l5 5-5 5" fill="none" stroke="#fff" stroke-width="2"/></svg></div>

<!-- team -->
<div class="abs team"></div>
<h2 class="abs section-h" style="left:0;top:2908px;width:1200px;text-align:center">OUR <span>TEAM</span></h2>
<div class="abs rule" style="left:561px;top:2966px;width:78px"></div>
<p class="abs team-sub">Sed ut perspiciatis unde omnis iste natus error sit voluptatem accusantium doloremque laudantium</p>

<div class="abs member" style="left:111px"><div class="member-photo" role="img" aria-label="Portrait of a team member" style="background:radial-gradient(ellipse 140px 150px at 115px 130px,rgba(190,150,120,.55),rgba(0,0,0,0)),linear-gradient(180deg,#d8d4ce 0%,#9a8f85 45%,#3a322c 100%)"></div><b>Jhon Smith</b><small>Lorem ipsum dolor</small></div>
<div class="abs member" style="left:359px"><div class="member-photo" role="img" aria-label="Portrait of a team member" style="background:radial-gradient(ellipse 130px 160px at 120px 120px,rgba(150,95,65,.6),rgba(0,0,0,0)),linear-gradient(180deg,#b8a899 0%,#6e5545 50%,#3a2a22 100%)"></div><b>Jhon Smith</b><small>Lorem ipsum dolor</small></div>
<div class="abs member" style="left:607px;border:none">
  <div class="member-photo" role="img" aria-label="Portrait of a team member" style="background:radial-gradient(ellipse 120px 140px at 115px 110px,rgba(90,85,80,.7),rgba(0,0,0,0)),linear-gradient(180deg,#2c2c2c,#121212);position:relative">
    <div class="abs" style="left:0;top:184px;width:231px;color:#fff;font-size:17px;font-weight:500">Jhon Smith</div>
    <div class="abs" style="left:0;top:207px;width:231px;color:#ddd;font-size:13px">Lorem ipsum dolor</div>
  </div>
  <div style="height:68px;background:var(--blue);color:#fff;font-size:13px;line-height:22px;padding-top:12px">Sed ut perspiciatis unde omnis<br>error sit voluptatem</div>
</div>
<div class="abs member" style="left:855px"><div class="member-photo" role="img" aria-label="Portrait of a team member" style="background:radial-gradient(ellipse 130px 150px at 115px 125px,rgba(200,150,115,.55),rgba(0,0,0,0)),linear-gradient(180deg,#8a7868 0%,#5e4a3c 50%,#33261f 100%)"></div><b>Jhon Smith</b><small>Lorem ipsum dolor</small></div>

<!-- footer -->
<footer class="abs footer"></footer>
<div class="abs f-brand"><i></i><span>Harlow Ridge<br>Financial Partners</span></div>
<div class="abs social" style="left:178px"></div>
<div class="abs social" style="left:221px"></div>
<div class="abs social" style="left:264px"></div>
<div class="abs social" style="left:307px"></div>
<div class="abs social" style="left:350px"></div>
<p class="abs f-copy" style="color:#fff">© Copyrights 2020-Company Name.All Rights Reserved.</p>

<h3 class="abs f-h" style="left:496px;color:#fff">QUICK LINKS</h3>
<ul class="abs f-links" style="color:#fff">
  <li>HOME</li><li>ABOUT US</li><li>SERVICES</li><li>PROJECT</li><li>BIO</li><li>CONTACT US</li>
</ul>

<h3 class="abs f-h" style="left:691px;color:#fff">NEWSLETTER SUBSCRIPTION</h3>
<p class="abs f-text" style="color:#fff">Northwake was founded in 2010 as a website dedicated to Gasoline Culture and all it entails</p>
<div class="abs f-input">Email :</div>
<div class="abs btn btn-blue" style="left:692px;top:3629px;width:108px;height:44px">Send</div>

</body>
</html>
```